Real Estate Website

Please refer to the attached document. It will be for a real estate agency specialising in commercial and residential sales. looking for Modern and minimalist, Sleek, professional, premium feel

```html
<!DOCTYPE html>
<html lang="en">
<head>
<meta charset="utf-8">
<title>Verano Group – Commercial &amp; Residential Property</title>
<link href="https://fonts.googleapis.com/css2?family=Poppins:wght@400;500;600;700&display=swap" rel="stylesheet">
<style>
:root{
  --orange:#f15a24;
  --orange-dark:#d9481a;
  --ink:#1f2a33;
  --slate:#27333d;
  --night:#1b1f24;
  --text:#4a5560;
  --muted:#8a939c;
  --line:#e3e6ea;
  --paper:#ffffff;
  --mist:#f3f4f6;
}
*{box-sizing:border-box;margin:0;padding:0}
html,body{width:1200px;height:5060px;overflow:hidden}
body{font-family:"Poppins",sans-serif;color:var(--text);background:var(--paper);position:relative;font-size:13px;line-height:1.6}
.abs{position:absolute}
a{color:inherit;text-decoration:none}
.accent{color:var(--orange)}
.btn{display:inline-flex;align-items:center;gap:8px;font-weight:500;font-size:13px;padding:10px 20px;border-radius:4px;color:#fff}
.btn-orange{background:var(--orange)}
.btn-dark{background:var(--ink)}
.eyebrow{display:flex;align-items:center;gap:8px;font-size:11px;font-weight:600;letter-spacing:.08em;text-transform:uppercase;color:var(--ink)}
.eyebrow .pin{width:14px;height:14px}
.center{justify-content:center}
h2{font-size:30px;font-weight:700;color:var(--ink);line-height:1.25}

.topbar{top:0;left:0;width:1200px;height:40px;background:var(--night);color:#fff;font-size:12px}
.topbar .tag{left:80px;top:11px}
.topbar .phone{left:770px;top:6px;background:var(--orange);padding:4px 16px;border-radius:3px;font-weight:600}
.topbar .socials{left:980px;top:13px;display:flex;gap:10px}
.topbar .socials span{width:14px;height:14px;border-radius:50%;background:#fff;opacity:.85}

.nav{top:40px;left:0;width:1200px;height:48px;background:#fff;font-size:13px;font-weight:500;color:var(--ink);box-shadow:0 2px 10px rgba(0,0,0,.05);z-index:3}
.nav .left{left:80px;top:14px;display:flex;gap:28px}
.nav .right{left:760px;top:14px;display:flex;gap:26px}
.nav .current{color:var(--orange)}
.brand{left:490px;top:30px;width:220px;height:80px;background:#fff;border-radius:0 0 10px 10px;display:flex;align-items:center;justify-content:center;gap:10px;z-index:4}
.brand .dot{width:22px;height:22px;border-radius:50%;background:var(--orange)}
.brand .name{font-size:24px;font-weight:700;color:var(--ink)}

.hero{top:88px;left:0;width:1200px;height:680px;overflow:hidden}
.hero .photo{inset:0;background:linear-gradient(180deg,#9fbcd6 0%,#c9d6e0 45%,#8ea0ad 70%,#5f6e78 100%)}
.hero .fade{inset:0;background:linear-gradient(90deg,#fff 0%,rgba(255,255,255,.9) 30%,rgba(255,255,255,0) 62%)}
.hero .copy{left:100px;top:130px;width:560px}
.hero .kicker{font-size:13px;font-weight:600;color:var(--ink);margin-bottom:8px}
.hero h1{font-size:40px;line-height:1.22;font-weight:700;color:var(--ink);text-transform:uppercase}
.hero .sub{margin-top:16px;font-size:15px;color:var(--ink);font-weight:500}
.hero .btn{margin-top:70px}
.hero .swoosh{left:0;bottom:0;width:1200px;height:200px}

.appraisal-media{left:100px;top:840px;width:420px;height:500px}
.appraisal-media .main{left:30px;top:0;width:380px;height:330px;background:linear-gradient(135deg,#6b5a4e,#c9b8a4 60%,#efe7dc);box-shadow:0 10px 30px rgba(0,0,0,.12)}
.appraisal-media .bar{left:0;top:40px;width:12px;height:280px;background:var(--orange)}
.appraisal-media .second{left:200px;top:220px;width:230px;height:230px;background:linear-gradient(135deg,#d9e2ea,#a7b6c2);border:6px solid #fff;box-shadow:0 10px 30px rgba(0,0,0,.15)}
.appraisal-media .badge{left:176px;top:220px;width:46px;height:46px;border-radius:50%;background:#fff;box-shadow:0 4px 14px rgba(0,0,0,.15);display:flex;align-items:center;justify-content:center}
.appraisal-copy{left:600px;top:860px;width:500px}
.appraisal-copy h2{margin:10px 0 16px;font-size:26px}
.appraisal-copy p{font-size:12.5px;margin-bottom:12px}
.appraisal-copy .btn{margin-top:18px}
.city-fade{left:860px;top:1170px;width:260px;height:150px;background:linear-gradient(180deg,rgba(225,229,233,0) 0%,rgba(225,229,233,.7) 100%)}

.services{top:1450px;left:0;width:1200px;height:560px;background:var(--mist)}
.services .head{top:70px;left:0;width:1200px;text-align:center}
.services h2{margin-top:8px;font-size:28px}
.cards{top:170px;left:140px;display:flex;gap:24px}
.card{width:290px;background:#fff;box-shadow:0 6px 20px rgba(0,0,0,.06)}
.card .img{height:170px}
.card .body{padding:18px 18px 22px}
.card h3{font-size:15px;font-weight:600;color:var(--ink);margin-bottom:6px}
.card p{font-size:12px;margin-bottom:12px}
.card .more{font-size:12px;font-weight:600;color:var(--ink);border-bottom:1px solid var(--ink)}

.why{top:2160px;left:0;width:1200px;height:600px}
.why .head{top:0;left:0;width:1200px;text-align:center}
.why h2{margin-top:8px;font-size:28px}
.ring{left:440px;top:130px;width:320px;height:320px}
.feature{width:300px}
.feature h4{font-size:15px;font-weight:600;color:var(--ink);margin-bottom:4px}
.feature p{font-size:12px}
.feature.l{text-align:right}
.ficon{width:54px;height:54px;flex:none;border-radius:50%;display:flex;align-items:center;justify-content:center}
.ficon.o{background:var(--orange)}
.ficon.d{background:var(--slate)}
.why .btn{left:506px;top:530px}

.who{top:2800px;left:0;width:1200px;height:500px}
.who .band{inset:0}
.who .copy{left:100px;top:90px;width:470px;color:#d8dde2}
.who h2{color:#fff;margin:10px 0 18px;font-size:28px}
.who .eyebrow{color:#fff}
.who p{font-size:12.5px;margin-bottom:12px}
.who .btn{margin-top:14px}
.who .photo{left:640px;top:60px;width:450px;height:330px;background:linear-gradient(135deg,#e8edf1,#b9c7d2 55%,#7f93a3);box-shadow:0 14px 40px rgba(0,0,0,.3)}

.reviews{top:3370px;left:0;width:1200px;height:420px}
.reviews .head{top:0;left:0;width:1200px;text-align:center}
.reviews h2{margin-top:8px;font-size:28px}
.quotes{top:110px;left:140px;display:flex;gap:24px}
.quote{width:290px;background:#fff;border:1px solid var(--line);box-shadow:0 6px 18px rgba(0,0,0,.05);padding:22px}
.quote .top{display:flex;justify-content:space-between;align-items:center}
.qmark{font-size:44px;font-weight:700;color:var(--ink);line-height:.7}
.stars{color:#f5a623;font-size:14px;letter-spacing:2px}
.gdot{width:16px;height:16px;border-radius:50%;background:var(--line)}
.quote p{font-size:12.5px;margin:14px 0 16px;color:var(--text)}
.quote .who-n{font-weight:600;color:var(--ink);font-size:13px}
.quote .role{font-size:11.5px;color:var(--muted)}
.arrow{width:30px;height:30px;border-radius:50%;background:var(--ink);display:flex;align-items:center;justify-content:center;top:195px}
.dots{top:330px;left:570px;display:flex;gap:8px}
.dots span{width:8px;height:8px;border-radius:50%;background:#cfd4d9}
.dots span.on{background:var(--orange)}

.contact{top:3860px;left:0;width:1200px;height:680px}
.contact .bg{inset:0}
.form{left:140px;top:140px;width:920px;height:480px;background:#fff;box-shadow:0 14px 40px rgba(0,0,0,.12);padding:40px 80px}
.form .eyebrow{justify-content:center}
.form h2{text-align:center;margin:8px 0 30px;font-size:26px}
.grid{display:grid;grid-template-columns:1fr 1fr;gap:16px}
.field{height:44px;border:1px solid var(--line);border-radius:3px;display:flex;align-items:center;gap:10px;padding:0 14px;font-size:12px;color:var(--muted)}
.field i{width:12px;height:12px;border-radius:50%;border:1.5px solid var(--muted)}
.field.msg{grid-column:1/3;height:100px;align-items:flex-start;padding-top:14px}
.submit{display:flex;justify-content:center;margin-top:22px}
.submit .btn{width:380px;justify-content:center}

.footer{top:4540px;left:0;width:1200px;height:520px}
.footer .bg{inset:0}
.f-brand{left:140px;top:140px;width:250px;color:#aab2ba}
.f-brand .logo{display:flex;align-items:center;gap:10px;margin-bottom:14px}
.f-brand .logo .dot{width:20px;height:20px;border-radius:50%;background:var(--orange)}
.f-brand .logo span{font-size:22px;font-weight:700;color:#fff}
.f-brand p{font-size:12px}
.follow{display:flex;align-items:center;gap:10px;margin-top:16px;font-size:12px;color:#fff}
.follow b{width:24px;height:24px;border-radius:50%;background:var(--orange)}
.f-col{top:140px;color:#aab2ba;font-size:12px}
.f-col h5{color:#fff;font-size:15px;font-weight:600;margin-bottom:14px}
.f-col li{list-style:none;margin-bottom:6px;display:flex;gap:8px;align-items:center}
.f-col li::before{content:"›";color:var(--orange)}
.f-contact li::before{content:none}
.f-contact .ic{width:26px;height:26px;border-radius:50%;background:var(--orange);flex:none;display:flex;align-items:center;justify-content:center}
.f-contact li{margin-bottom:14px;align-items:flex-start}
.copyright{left:0;top:470px;width:1200px;text-align:center;font-size:11px;color:#8a939c;border-top:1px solid #2e343b;padding-top:16px}
</style>
</head>
<body>

<svg width="0" height="0" style="position:absolute">
  <defs>
    <symbol id="pin" viewBox="0 0 24 24"><path d="M12 2a7 7 0 0 0-7 7c0 5 7 13 7 13s7-8 7-13a7 7 0 0 0-7-7z" fill="#f15a24"/><circle cx="12" cy="9" r="2.6" fill="#fff"/></symbol>
    <symbol id="arrow" viewBox="0 0 24 24"><path d="M7 17L17 7M9 7h8v8" stroke="#fff" stroke-width="2.2" fill="none" stroke-linecap="round"/></symbol>
  </defs>
</svg>

<div class="abs topbar">
  <span class="abs tag">Discover The Real Value of Investments Your Property</span>
  <span class="abs phone">Phone No: (03) 9000 4821</span>
  <div class="abs socials"><span></span><span></span><span></span></div>
</div>

<nav class="abs nav">
  <div class="abs left"><a class="current">Home</a><a>Commercial / Industrial</a><a>Residential</a></div>
  <div class="abs right"><a>Business Sales</a><a>About Us</a><a>Info ▾</a><a>Contact Us</a></div>
</nav>
<div class="abs brand"><span class="dot"></span><span class="name">Verano Group</span></div>

<section class="abs hero">
  <div class="abs photo" role="img" aria-label="City skyline beside a river with a stone bridge at dusk"></div>
  <div class="abs fade"></div>
  <div class="abs copy">
    <div class="kicker">Specialists In</div>
    <h1>Commercial &amp; Industrial <span class="accent">Property Trusted In</span> Residential Property</h1>
    <p class="sub">Maximising Returns, Protecting Investments, Delivering Expert Property Advice</p>
    <a class="btn btn-orange">Book an Appraisal <svg width="12" height="12"><use href="#arrow"/></svg></a>
  </div>
  <svg class="abs swoosh" viewBox="0 0 1200 200" preserveAspectRatio="none">
    <path d="M0 200 L0 150 C400 200 800 160 1200 60 L1200 200 Z" fill="#f15a24"/>
    <path d="M0 200 L0 170 C420 210 820 180 1200 100 L1200 200 Z" fill="#fff"/>
  </svg>
</section>

<div class="abs appraisal-media">
  <div class="abs bar"></div>
  <div class="abs main" role="img" aria-label="Business handshake over a desk with property documents"></div>
  <div class="abs second" role="img" aria-label="Agent meeting clients in a bright office"></div>
  <div class="abs badge"><svg width="22" height="22"><use href="#pin"/></svg></div>
</div>
<div class="abs appraisal-copy">
  <div class="eyebrow"><svg class="pin"><use href="#pin"/></svg>Book An Appraisal</div>
  <h2>Discover The Real Value Of <span class="accent">Your Property</span></h2>
  <p>At Verano Group, we don't just provide standard appraisals — we deliver strategic, insight-driven reports that uncover the true drivers of your property's worth. Whether it's commercial, industrial, or residential, our expertise ensures you see the full picture.</p>
  <p>From market trends and rental potential to investment performance and future growth opportunities, our tailored reports give you clarity, confidence, and actionable insights.</p>
  <p>Book a confidential consultation today and gain the expert guidance you need to maximise returns and make smarter property decisions.</p>
  <a class="btn btn-dark">Schedule Consultation <svg width="12" height="12"><use href="#arrow"/></svg></a>
</div>
<div class="abs city-fade" role="img" aria-label="Faint outline of city buildings"></div>

<section class="abs services">
  <div class="abs head">
    <div class="eyebrow center"><svg class="pin"><use href="#pin"/></svg>What We Do</div>
    <h2>Property Management, <span class="accent">Sales &amp; Leasing</span></h2>
  </div>
  <div class="abs cards">
    <article class="card">
      <div class="img" role="img" aria-label="Modern commercial office building" style="background:linear-gradient(160deg,#a9c3da,#e6eef4 60%,#9aa6ae)"></div>
      <div class="body"><h3>Commercial &amp; Industrial</h3><p>Specialist management and leasing of premium commercial and industrial assets trusted by investors and developers.</p><a class="more">Learn More ↗</a></div>
    </article>
    <article class="card">
      <div class="img" role="img" aria-label="Brick family home with front garden" style="background:linear-gradient(160deg,#b9cde0,#8e5d45 60%,#5f7a4e)"></div>
      <div class="body"><h3>Residential Property</h3><p>Expert residential property management and sales services with proven results and exceptional client outcomes.</p><a class="more">Learn More ↗</a></div>
    </article>
    <article class="card">
      <div class="img" role="img" aria-label="Advisor reviewing property reports with a client" style="background:linear-gradient(160deg,#d7d0c6,#a58f78 60%,#6f625a)"></div>
      <div class="body"><h3>Property Advisory</h3><p>Comprehensive financial reporting, budgeting, and expense management to optimise cash flow and returns.</p><a class="more">Learn More ↗</a></div>
    </article>
  </div>
</section>

<section class="abs why">
  <div class="abs head">
    <div class="eyebrow center"><svg class="pin"><use href="#pin"/></svg>Why Choose Us</div>
    <h2>Commercial &amp; Industrial Property <span class="accent">Management &amp; Leasing</span></h2>
  </div>
  <svg class="abs ring" viewBox="0 0 320 320">
    <circle cx="160" cy="160" r="150" fill="none" stroke="#27333d" stroke-width="3" stroke-dasharray="6 8"/>
    <circle cx="160" cy="160" r="118" fill="#fff" stroke="#e3e6ea" stroke-width="2"/>
    <circle cx="160" cy="112" r="14" fill="#f15a24"/>
    <text x="160" y="172" text-anchor="middle" font-family="Poppins, sans-serif" font-size="28" font-weight="700" fill="#1f2a33">Verano</text>
    <text x="160" y="200" text-anchor="middle" font-family="Poppins, sans-serif" font-size="28" font-weight="700" fill="#1f2a33">Group</text>
  </svg>
  <div class="abs feature l" style="left:80px;top:150px">
    <div style="display:flex;gap:16px;align-items:flex-start"><div><h4>Sector Expertise</h4><p>Deep knowledge across medical, healthcare, franchise, retail and industrial sectors, enabling tailored strategies for each asset class.</p></div><div class="ficon o"><svg width="22" height="22"><use href="#pin"/></svg></div></div>
  </div>
  <div class="abs feature" style="left:820px;top:150px">
    <div style="display:flex;gap:16px;align-items:flex-start"><div class="ficon d"><svg width="22" height="22" viewBox="0 0 24 24"><path d="M5 12l4 4 10-10" stroke="#fff" stroke-width="2.4" fill="none"/></svg></div><div><h4>Bespoke Solutions</h4><p>Every property is unique. We craft customised management and leasing strategies aligned with your objectives and market conditions.</p></div></div>
  </div>
  <div class="abs feature l" style="left:80px;top:340px">
    <div style="display:flex;gap:16px;align-items:flex-start"><div><h4>Proactive Asset Management</h4><p>Beyond operations, we actively enhance value, mitigate risk and secure the right tenants.</p></div><div class="ficon d"><svg width="22" height="22" viewBox="0 0 24 24"><path d="M4 18l6-6 4 4 6-8" stroke="#fff" stroke-width="2.4" fill="none"/></svg></div></div>
  </div>
  <div class="abs feature" style="left:820px;top:340px">
    <div style="display:flex;gap:16px;align-items:flex-start"><div class="ficon o"><svg width="22" height="22" viewBox="0 0 24 24"><circle cx="12" cy="10" r="5" stroke="#fff" stroke-width="2.2" fill="none"/><path d="M9 14l-2 7 5-3 5 3-2-7" stroke="#fff" stroke-width="2" fill="none"/></svg></div><div><h4>Professional Excellence</h4><p>Integrity, precision, and industry-leading best practice in everything we do.</p></div></div>
  </div>
  <a class="abs btn btn-orange">Book An Appraisal <svg width="12" height="12"><use href="#arrow"/></svg></a>
</section>

<section class="abs who">
  <svg class="abs band" width="1200" height="500" viewBox="0 0 1200 500" preserveAspectRatio="none">
    <polygon points="0,30 1200,0 1200,470 0,500" fill="#27333d"/>
    <polygon points="0,30 420,19 0,60" fill="#f15a24"/>
  </svg>
  <div class="abs copy">
    <div class="eyebrow"><svg class="pin"><use href="#pin"/></svg>Who We Are</div>
    <h2>We Are Recognised As <span class="accent">A Trusted</span></h2>
    <p>At Verano Group, we are recognised as a trusted authority in commercial and residential property management, sales, and leasing. Property owners, investors and developers turn to us for our proven expertise, discretion, and consistent results.</p>
    <p>Our mission is to set the standard for excellence in property services. Guided by innovation, integrity, and strategic execution, we deliver outcomes that protect assets, maximise returns and create enduring value for our clients.</p>
    <a class="btn btn-orange">Schedule Consultation <svg width="12" height="12"><use href="#arrow"/></svg></a>
  </div>
  <div class="abs photo" role="img" aria-label="Team presenting charts in a modern meeting room"></div>
</section>

<section class="abs reviews">
  <div class="abs head">
    <div class="eyebrow center"><svg class="pin"><use href="#pin"/></svg>Testimonials</div>
    <h2>What Our Clients Say <span class="accent">About Us</span></h2>
  </div>
  <div class="abs arrow" style="left:90px"><svg width="12" height="12" viewBox="0 0 24 24"><path d="M15 5l-7 7 7 7" stroke="#fff" stroke-width="2.6" fill="none"/></svg></div>
  <div class="abs arrow" style="left:1080px"><svg width="12" height="12" viewBox="0 0 24 24"><path d="M9 5l7 7-7 7" stroke="#fff" stroke-width="2.6" fill="none"/></svg></div>
  <div class="abs quotes">
    <article class="quote"><div class="top"><span class="qmark">“</span><span class="stars">★★★★★</span><span class="gdot"></span></div><p>"Their team handled our property with care and real insight. Leasing was quick, reporting was clear, and returns have grown steadily every single year."</p><div class="who-n">Clara Bennet</div><div class="role">Asset Portfolio Manager</div></article>
    <article class="quote"><div class="top"><span class="qmark">“</span><span class="stars">★★★★★</span><span class="gdot"></span></div><p>"Their team handled our property with care and real insight. Leasing was quick, reporting was clear, and returns have grown steadily every single year."</p><div class="who-n">Imogen Hart</div><div class="role">Senior Leasing Specialist</div></article>
    <article class="quote"><div class="top"><span class="qmark">“</span><span class="stars">★★★★★</span><span class="gdot"></span></div><p>"Their team handled our property with care and real insight. Leasing was quick, reporting was clear, and returns have grown steadily every single year."</p><div class="who-n">Daniel Ruiz</div><div class="role">Regional Property Director</div></article>
  </div>
  <div class="abs dots"><span class="on"></span><span></span><span></span><span></span></div>
</section>

<section class="abs contact">
  <svg class="abs bg" width="1200" height="680" viewBox="0 0 1200 680" preserveAspectRatio="none">
    <rect width="1200" height="680" fill="#f3f4f6"/>
    <polygon points="0,0 1200,80 1200,280 0,200" fill="#f15a24"/>
    <polygon points="0,0 1200,80 1200,110 0,30" fill="#d9481a"/>
  </svg>
  <div class="abs form">
    <div class="eyebrow"><svg class="pin"><use href="#pin"/></svg>Contact Us</div>
    <h2>Ready To Discuss Your <span class="accent">Property Goals?</span></h2>
    <div class="grid">
      <div class="field"><i></i>First Name</div>
      <div class="field"><i></i>Last Name</div>
      <div class="field"><i></i>Your Email</div>
      <div class="field"><i></i>Phone</div>
      <div class="field msg"><i></i>Your Message</div>
    </div>
    <div class="submit"><a class="btn btn-dark">Submit Now <svg width="12" height="12"><use href="#arrow"/></svg></a></div>
  </div>
</section>

<footer class="abs footer">
  <svg class="abs bg" width="1200" height="520" viewBox="0 0 1200 520" preserveAspectRatio="none">
    <polygon points="0,60 1200,0 1200,520 0,520" fill="#1b1f24"/>
    <polygon points="700,35 1200,10 1200,30 700,55" fill="#f15a24"/>
  </svg>
  <div class="abs f-brand">
    <div class="logo"><span class="dot"></span><span>Verano Group</span></div>
    <p>Trusted property partners for sales, leasing and management across commercial and residential markets.</p>
    <div class="follow">Follow Us: <b></b><b></b><b></b></div>
  </div>
  <div class="abs f-col" style="left:460px">
    <h5>Quick Links</h5>
    <ul><li>Home</li><li>Commercial / Industrial</li><li>Residential</li><li>Business Sales</li><li>About Us</li><li>Info</li><li>Contact Us</li></ul>
  </div>
  <div class="abs f-col" style="left:660px">
    <h5>Key Offerings</h5>
    <ul><li>Business listings</li><li>Appraisal report</li><li>What we do</li><li>Who we are</li></ul>
  </div>
  <div class="abs f-col f-contact" style="left:850px;width:240px">
    <h5>Contact Us</h5>
    <ul>
      <li><span class="ic"><svg width="14" height="14"><use href="#pin"/></svg></span>48 Harbour Lane, Southbank VIC 3000</li>
      <li><span class="ic"><svg width="12" height="12" viewBox="0 0 24 24"><path d="M6 3l4 4-2 3c1 2 3 4 6 6l3-2 4 4-3 3C10 21 3 14 3 6z" fill="#fff"/></svg></span>Phone: (03) 9000 4821</li>
      <li><span class="ic"><svg width="12" height="12" viewBox="0 0 24 24"><rect x="3" y="6" width="18" height="12" fill="none" stroke="#fff" stroke-width="2"/><path d="M3 6l9 7 9-7" stroke="#fff" stroke-width="2" fill="none"/></svg></span>hello@veranogroup.example</li>
    </ul>
  </div>
  <div class="abs copyright">© 2025 Verano Group. All Rights Reserved.</div>
</footer>

</body>
</html>
```